Custom Woodworking and Rock Design

We specialize in original, high quality, wood and rock art. It’s should be self explanatory ask questions if you need. Your team designing a logo. Furniture is custom made to order. Rocks are designed depending on consumer needs. Wood and rock can also be combined for custom work. Painted rocks on vintage wood. Custom chairs and cabinets. Artistic rocks for multiple uses:garden, magnets, custom. All ideas and requests are welcome.

Target Market(s)

All

Contact Information for Business Card

Mara Voss
Talbertstonecraft@mailbrook.net

Font styles to use
Sans Serif

Requirements
Must have
• Clear lettering
Nice to have
• Eye catching
Should not have
• Blurr

```html
<!DOCTYPE html>
<html lang="en">
<head>
<meta charset="utf-8">
<title>Mara Voss — Business Card</title>
<link rel="stylesheet" href="https://fonts.googleapis.com/css2?family=Open+Sans:wght@400;600&display=swap">
<style>
  :root {
    --page-bg: #e9e6e2;
    --wood-light: #6e5a48;
    --wood-mid: #5a4838;
    --wood-dark: #463628;
    --photo-fence: #7d7064;
    --photo-soil: #4f4339;
    --photo-rock: #77736d;
    --accent-blue: #4a80d2;
    --text-light: #f4f1ec;
    --rule: #d8d2ca;
  }
  * { margin: 0; padding: 0; box-sizing: border-box; }
  html, body {
    width: 1200px;
    height: 900px;
    overflow: hidden;
    background: var(--page-bg);
  }
  .canvas {
    position: relative;
    width: 1200px;
    height: 900px;
  }
  .business-card {
    position: absolute;
    left: 100px;
    top: 165px;
    width: 1000px;
    height: 570px;
    overflow: hidden;
    box-shadow: 0 12px 30px rgba(0,0,0,0.25);
  }
  .card-art {
    position: absolute;
    inset: 0;
    display: block;
  }
  .contact-block {
    position: absolute;
    left: 110px;
    top: 248px;
    font-family: "Open Sans", sans-serif;
  }
  .contact-name {
    color: var(--accent-blue);
    font-weight: 600;
    font-size: 34px;
    letter-spacing: 0.5px;
    line-height: 1;
  }
  .contact-rule {
    width: 215px;
    height: 1.5px;
    background: var(--rule);
    margin: 18px 0 20px;
  }
  .contact-email {
    color: var(--text-light);
    font-weight: 400;
    font-size: 22px;
    letter-spacing: 0.4px;
    line-height: 1;
  }
</style>
</head>
<body>
<main class="canvas">
  <section class="business-card">
    <svg class="card-art" width="1000" height="570" viewBox="0 0 1000 570">
      <defs>
        <linearGradient id="wood-panel" x1="0" y1="0" x2="1" y2="0.3">
          <stop offset="0" stop-color="var(--wood-dark)"/>
          <stop offset="0.45" stop-color="var(--wood-light)"/>
          <stop offset="1" stop-color="var(--wood-mid)"/>
        </linearGradient>
        <linearGradient id="rock-photo" x1="0" y1="0" x2="0" y2="1">
          <stop offset="0" stop-color="var(--photo-fence)"/>
          <stop offset="0.35" stop-color="var(--photo-soil)"/>
          <stop offset="0.75" stop-color="var(--photo-rock)"/>
          <stop offset="1" stop-color="#a9a6a0"/>
        </linearGradient>
      </defs>
      <rect class="wood-panel" width="1000" height="570" fill="url(#wood-panel)" role="img" aria-label="Wood grain texture background"/>
      <polygon class="photo-panel" points="585,0 1000,0 1000,570 730,570" fill="url(#rock-photo)" role="img" aria-label="Photo of a rock garden border with a painted flag rock in front of a wooden fence"/>
      <line class="divider" x1="585" y1="0" x2="730" y2="570" stroke="var(--accent-blue)" stroke-width="5"/>
    </svg>
    <div class="contact-block">
      <p class="contact-name">Mara Voss</p>
      <div class="contact-rule"></div>
      <p class="contact-email">Talbertstonecraft@mailbrook.net</p>
    </div>
  </section>
</main>
</body>
</html>
```